Business Card - Business Consultancy

Newly Established Company, specializing in Business Consultancy, Human Resource Management, Talent Acquisition and Payroll Solutions.

We need a Business card design which portrays "elegance" and a very sleek yet business-like design. We would like a nice blue trimming (which goes well with the logo) to separate the content of the business card at the top. We would also like to see the design using the color silver either as a background or incorporated into it.

The final design should be a Business card which has colors matching the logo; a nice font; the above-mentioned specifics that adheres to the theme of "a stylish and professional business"

FYI: please do not have too fanciful designs.

Industry/Entity Type

Business Consultant

Contact Information for Business Card

Darren Lim
Business Development Director
Arbor Talent Consulting Private Limited
27 Wexley Street, #05-03B
Harbourgate Trade Building
Singapore 059317
Mobile : (+65) 98354417
Email : dlim@arbortalent-advisory.com
Alternative : arbortalentadvisory@mailbox-example.com

Requirements
Must have
• Nice Blue Trimming matching Logo which separates content, see attached
• Design incorporates either a silver background or the use of the color silver
Should not have
• No Fanciful Designs
• No Childish Designs
• No Overly Complicated Designs

```html
<!DOCTYPE html>
<html lang="en">
<head>
<meta charset="utf-8">
<title>Arbor Talent Consulting – Business Card</title>
<link href="https://fonts.googleapis.com/css2?family=Open+Sans:wght@400;600;700&display=swap" rel="stylesheet">
<style>
  :root {
    --stage: #e4e6e8;
    --card: #ffffff;
    --brand-blue: #1479c4;
    --brand-green: #7dc32a;
    --ink: #222222;
    --ink-soft: #333333;
    --shadow: rgba(0, 0, 0, 0.18);
  }
  * { margin: 0; padding: 0; box-sizing: border-box; }
  html, body {
    width: 1200px; height: 844px; overflow: hidden;
    background: var(--stage);
    font-family: "Open Sans", sans-serif;
  }
  .stage {
    position: relative; width: 1200px; height: 844px;
    display: flex; align-items: center; justify-content: center; gap: 60px;
  }
  .card {
    position: relative; width: 520px; height: 300px;
    background: var(--card);
    box-shadow: 0 10px 24px var(--shadow);
    overflow: hidden;
  }
  /* Contact side */
  .contact-card .trim-top {
    position: absolute; left: 0; top: 0; width: 100%; height: 14px;
    background: var(--brand-green);
  }
  .contact-card .trim-bottom {
    position: absolute; left: 0; bottom: 0; width: 100%; height: 18px;
    background: var(--brand-blue);
  }
  .contact-details {
    position: absolute; left: 0; right: 0; top: 44px;
    text-align: center; color: var(--ink-soft); font-size: 14px; line-height: 1.4;
  }
  .contact-name { color: var(--brand-blue); font-size: 18px; font-weight: 600; line-height: 1.2; }
  .contact-role { margin-bottom: 16px; }
  .contact-address { margin-bottom: 22px; }
  .contact-line { display: flex; align-items: center; justify-content: center; gap: 6px; font-size: 15px; }
  .contact-line svg { flex: none; }
  /* Brand side */
  .brand-tab-green {
    position: absolute; right: 0; top: 22px; width: 30px; height: 30px;
    background: var(--brand-green);
  }
  .brand-tab-blue {
    position: absolute; left: 0; top: 150px; width: 24px; height: 48px;
    background: var(--brand-blue);
  }
  .brand-lockup {
    position: absolute; left: 0; right: 0; top: 88px;
    display: flex; align-items: center; justify-content: center; gap: 14px;
  }
  .brand-dot { width: 60px; height: 60px; border-radius: 50%; background: var(--brand-blue); }
  .brand-name { color: var(--ink); font-size: 30px; font-weight: 700; line-height: 1.05; }
  .brand-services {
    position: absolute; left: 0; right: 0; top: 186px;
    text-align: center; color: var(--ink); font-size: 14px; font-weight: 600;
  }
</style>
</head>
<body>
<main class="stage">
  <section class="card contact-card">
    <div class="trim-top"></div>
    <div class="contact-details">
      <p class="contact-name">Darren Lim</p>
      <p class="contact-role">Business Development Director</p>
      <p class="contact-address">27 Wexley Street, #05-03B<br>Harbourgate Trade Building<br>Singapore 059317</p>
      <p class="contact-line">
        <svg width="12" height="12" viewBox="0 0 24 24" aria-hidden="true"><path fill="#1479c4" d="M6.6 10.8a15.1 15.1 0 0 0 6.6 6.6l2.2-2.2a1 1 0 0 1 1-.25 11.4 11.4 0 0 0 3.6.6 1 1 0 0 1 1 1V20a1 1 0 0 1-1 1A17 17 0 0 1 3 4a1 1 0 0 1 1-1h3.5a1 1 0 0 1 1 1c0 1.25.2 2.45.6 3.6a1 1 0 0 1-.25 1z"/></svg>
        (+65) 98354417
      </p>
      <p class="contact-line">
        <svg width="13" height="10" viewBox="0 0 26 20" aria-hidden="true"><rect width="26" height="20" rx="2" fill="#1479c4"/><path d="M2 3l11 8 11-8" stroke="#fff" stroke-width="2" fill="none"/></svg>
        dlim@arbortalent-advisory.com
      </p>
      <p class="contact-line">
        <svg width="13" height="10" viewBox="0 0 26 20" aria-hidden="true"><rect width="26" height="20" rx="2" fill="#1479c4"/><path d="M2 3l11 8 11-8" stroke="#fff" stroke-width="2" fill="none"/></svg>
        arbortalentadvisory@mailbox-example.com
      </p>
    </div>
    <div class="trim-bottom"></div>
  </section>

  <section class="card brand-card">
    <div class="brand-tab-green"></div>
    <div class="brand-tab-blue"></div>
    <div class="brand-lockup">
      <div class="brand-dot"></div>
      <p class="brand-name">Arbor Talent<br>Consulting</p>
    </div>
    <p class="brand-services">Recruitment | HR Solutions | Business Consultancy</p>
  </section>
</main>
</body>
</html>
```